Quill Harbor (IT/Network Services)

Quill Harbor, LLC provides technology services to small and medium businesses. Essentially, anytime you've every thought your business might need an "IT guy" to handle something you could instead call us to handle it. Basically, you can outsource your IT needs to us.

This is a brand new company and so we'll need a brand new website. I'd like to use WordPress to handle the site since that will make things easier for me to maintain in the long run.

The site should include a, more-or-less, static front page with the dynamic data occurring on pages linked from a navigational area.

I have a logo already designed that I would like to see used in the design. The one with "white" in the title is the official logo, just added some other versions for your perusal.

Color queues from the logo but feel free to add other colors where applicable.

The site should feel somewhat corporate but with a "younger" slant (something a 25-35 year old would enjoy).

Pages (either to be added initially or by me after design completion):
"About" section - includes company history, business philosophy, etc.
"Services" section - service options, service approach, service specifics
"Testimonials" section - (eventually)
"News" section - (eventually) industry news, company news, events, blog
Contact Links

Websites to view:
The two largest local competitors:
http://www.brightmarsh-tech.example/
http://www.kelvarworks.example/
Other local competitors:
http://www.tpbllc.example/
http://www.morrowfield.example/

Other info you might find useful:
Domain: qhllc.example
Address:
417 Elm Row S
Suite 512B
Nashville, TN 37288
Phone: 615-555-0187
Emails available for use/display:
info@qhllc.example
sales@qhllc.example

Target Market(s)

Our target clients are mainly small businesses (25 or less computer users) which means we're looking at a lot of start-ups or younger companies. We'll be interacting with many entrepreneurs and young business owners.

Requirements
Must have
• Need full WP theme (not a mockup)

```html
<!DOCTYPE html>
<html lang="en">
<head>
<meta charset="utf-8">
<title>Quill Harbor — IT Services</title>
<link href="https://fonts.googleapis.com/css2?family=Signika:wght@400;600&family=Oswald:wght@400;500&family=Arimo:wght@400;700&display=swap" rel="stylesheet">
<style>
:root{
  --orange:#f07a12;
  --orange-deep:#e25a0c;
  --orange-light:#fba22a;
  --blue:#1a5fc4;
  --blue-dark:#14489a;
  --ink:#4a4c50;
  --text:#3a3b3e;
  --muted:#6d6f73;
  --page:#e8e9eb;
  --band:#d9dadc;
  --base:#c9cacc;
  --nav:#7e8185;
  --nav-active:#5e6165;
  --white:#ffffff;
  --logo-box:#e6e7e9;
}
*{box-sizing:border-box;margin:0;padding:0}
html,body{width:840px;height:1200px;overflow:hidden}
body{position:relative;background:var(--page);font-family:"Arimo",Arial,sans-serif;color:var(--text)}
.abs{position:absolute}

.hero{left:0;top:0;width:840px;height:377px;background:radial-gradient(ellipse at 45% 60%,var(--orange-light) 0%,var(--orange) 45%,var(--orange-deep) 100%)}
.hero-photo{left:200px;top:30px;width:460px;height:347px;background:linear-gradient(135deg,rgba(255,255,255,.55),rgba(60,60,60,.35));border-radius:120px 120px 0 0;opacity:.55}
.brand{left:80px;top:0;width:174px;height:133px;background:var(--logo-box);display:flex;align-items:center;justify-content:center;gap:8px}
.brand-dot{width:16px;height:16px;border-radius:50%;background:var(--orange)}
.brand-name{font-family:"Signika",sans-serif;font-weight:600;font-size:20px;color:var(--nav)}
.headline{left:424px;top:80px;width:400px;font-family:"Signika",sans-serif;font-weight:600;font-size:39px;line-height:45px;color:var(--logo-box)}
.cta{left:427px;top:185px;width:178px;height:40px;background:var(--blue);border:3px solid var(--white);color:var(--white);font-family:"Signika",sans-serif;font-weight:600;font-size:18px;display:flex;align-items:center;justify-content:center}

.nav{left:0;top:377px;width:840px;height:33px;background:var(--nav);border-bottom:1px solid #9a9c9f}
.nav-item{position:absolute;top:0;height:33px;display:flex;align-items:center;justify-content:center;font-family:"Oswald",sans-serif;font-size:14px;color:var(--white);border-right:1px solid #909296}
.nav-item.active{background:var(--nav-active);color:#b7b9bc}
.search{left:602px;top:384px;width:160px;height:23px;background:var(--white);display:flex;align-items:center;padding-left:8px;font-size:11px;color:#8a8c90}
.search-btn{left:740px;top:384px;width:22px;height:23px;background:var(--blue);display:flex;align-items:center;justify-content:center}

.section-title{font-family:"Signika",sans-serif;font-weight:600;color:var(--ink);font-size:21px;line-height:25px}
.feature{left:80px;width:420px;display:flex;gap:14px;align-items:center}
.feature-num{flex:none;width:35px;height:35px;border-radius:50%;color:var(--white);font-family:"Signika",sans-serif;font-size:22px;display:flex;align-items:center;justify-content:center}
.feature-text{font-size:10px;line-height:13px;color:var(--text)}
.news{left:540px;top:482px;width:220px}
.news-item{margin-bottom:10px;font-size:9.5px;line-height:12.8px}
.news-date{color:var(--orange-deep);text-decoration:underline}

.card{top:703px;width:155px}
.card-img{width:144px;height:81px;background:linear-gradient(135deg,#2a6fc0,#0d2a52)}
.card-title{margin-top:20px;font-family:"Signika",sans-serif;font-weight:600;font-size:19px;color:var(--ink)}
.card-text{margin-top:6px;font-size:9px;line-height:14px;color:var(--text)}
.btn{margin-top:16px;width:68px;height:23px;border:1px solid #cfd0d2;background:#f4f4f5;font-size:9.5px;font-weight:700;color:var(--ink);display:flex;align-items:center;justify-content:center;border-radius:2px}
.btn.primary{background:linear-gradient(var(--blue),var(--blue-dark));color:var(--white);border-color:var(--blue-dark)}

.footer{left:0;top:976px;width:840px;height:150px;background:var(--band)}
.service-list{width:112px;list-style:none}
.service-list li{font-size:8.5px;color:var(--muted);height:20px;line-height:18px;border-bottom:1px dotted #b3b5b8;padding-left:10px;position:relative}
.service-list li::before{content:"";position:absolute;left:0;top:6px;border-left:5px solid #9a9c9f;border-top:3px solid transparent;border-bottom:3px solid transparent}
.newsletter-text{font-size:8.5px;line-height:13px;color:var(--muted)}
.email{left:542px;top:1074px;width:143px;height:25px;background:var(--white);font-size:10px;color:var(--muted);display:flex;align-items:center;padding-left:10px}
.subscribe{left:688px;top:1074px;width:72px;height:25px;background:var(--blue);color:var(--white);font-family:"Oswald",sans-serif;font-size:13px;display:flex;align-items:center;justify-content:center}

.base{left:0;top:1124px;width:840px;height:76px;background:var(--base);border-top:5px solid #aeb0b3}
.legal{left:80px;top:1148px;font-size:8.5px;line-height:17px;color:var(--muted)}
.social{top:1146px;width:24px;height:24px;background:#eeeff0;border-radius:3px}
</style>
</head>
<body>

<header>
  <div class="abs hero"></div>
  <div class="abs hero-photo" role="img" aria-label="Young professional working on a laptop"></div>
  <div class="abs brand"><span class="brand-dot"></span><span class="brand-name">Quill Harbor</span></div>
  <h1 class="abs headline">Does your business needs an “IT Guy?”</h1>
  <div class="abs cta">CONTACT US NOW</div>
</header>

<nav class="abs nav">
  <span class="nav-item active" style="left:80px;width:63px">HOME</span>
  <span class="nav-item" style="left:143px;width:85px">ABOUT US</span>
  <span class="nav-item" style="left:228px;width:83px">SERVICES</span>
  <span class="nav-item" style="left:311px;width:98px">TESTIMONAL</span>
  <span class="nav-item" style="left:409px;width:71px">NEWS</span>
  <span class="nav-item" style="left:480px;width:100px">CONTACT US</span>
</nav>
<div class="abs search">Search...</div>
<div class="abs search-btn">
  <svg width="13" height="13" viewBox="0 0 13 13"><circle cx="7.5" cy="5" r="3.5" fill="none" stroke="#fff" stroke-width="1.6"/><line x1="5" y1="7.5" x2="1.5" y2="11.5" stroke="#fff" stroke-width="2"/></svg>
</div>

<main>
  <h2 class="abs section-title" style="left:80px;top:449px;width:440px">What we can do for you through Information Technology:</h2>

  <div class="abs feature" style="top:516px">
    <span class="feature-num" style="background:var(--blue)">1</span>
    <p class="feature-text">Mam libero tempore massasoluta nobis est eligendi omnis voluasassumenda est, omnis dolo- reseereeledusempquibusdamet aurerum odes necessitatibus saepe eveniet utoluptates estu</p>
  </div>
  <div class="abs feature" style="top:568px">
    <span class="feature-num" style="background:var(--orange-deep)">2</span>
    <p class="feature-text">Sibero tempore massasoluta nobis est eligendi omnis voluasassumenda est, omnis dolore- sereeledusempquibusdamet aurerum odes necessitatibus saepe eveniet utoluptates estu repudiandae sintet molestiae non recusandaeltaque earum.</p>
  </div>
  <div class="abs feature" style="top:620px">
    <span class="feature-num" style="background:#6d6f73">3</span>
    <p class="feature-text">Mam libero tempore massasoluta nobis est eligendi omnis voluasassumenda est, omnis dolo- reseereeledusempquibusdamet aurerum odes necessitatibus saepe eveniet utoluptates estu</p>
  </div>

  <h2 class="abs section-title" style="left:540px;top:450px">Quill Harbor Latest News:</h2>
  <div class="abs news">
    <p class="news-item"><span class="news-date">20.05.2012:</span><br>massasoluta nobis est eligendi omnis voluasassumenda est, omnis doloreser- eeledusempquibusdamet aurerum odesom</p>
    <p class="news-item"><span class="news-date">20.05.2012:</span><br>massasoluta nobis est eligendi omnis voluasassumenda est, omnis doloreser- eeledusempquibusdamet aurerum odes nece</p>
    <p class="news-item"><span class="news-date">20.05.2012:</span><br>massasoluta nobis est eligendi omnis voluasassumenda est, omnis doloreser- eeledusempquibusdamet aurerum odesom</p>
  </div>

  <article class="abs card" style="left:80px">
    <div class="card-img" role="img" aria-label="Blue-lit network of computers"></div>
    <h3 class="card-title">Networking</h3>
    <p class="card-text">Mam libero tempore massasoluta nobis est eligendi omnis voluasas sumenda est, omnis doloresereele dusempquibusdamet.</p>
    <div class="btn primary">Read More</div>
  </article>
  <article class="abs card" style="left:249px">
    <div class="card-img" style="background:linear-gradient(135deg,#e9e6e0,#8a7a6a)" role="img" aria-label="Support staff wearing headsets"></div>
    <h3 class="card-title">Technical Support</h3>
    <p class="card-text">Mam libero tempore massasoluta nobis est eligendi omnis voluasas sumenda est, omnis doloresereele dusempquibusdamet.</p>
    <div class="btn">Read More</div>
  </article>
  <article class="abs card" style="left:418px">
    <div class="card-img" style="background:linear-gradient(135deg,#e4e6ea,#3c4350)" role="img" aria-label="Business team gathered around a laptop"></div>
    <h3 class="card-title">Project Management</h3>
    <p class="card-text">Mam libero tempore massasoluta nobis est eligendi omnis voluasas sumenda est, omnis doloresereele dusempquibusdamet.</p>
    <div class="btn">Read More</div>
  </article>
  <article class="abs card" style="left:607px">
    <div class="card-img" style="background:linear-gradient(135deg,#f2f2f2,#2b2c2e)" role="img" aria-label="Hands typing on a laptop keyboard"></div>
    <h3 class="card-title">IT Solutions</h3>
    <p class="card-text">Mam libero tempore massasoluta nobis est eligendi omnis voluasas sumenda est, omnis doloresereele dusempquibusdamet.</p>
    <div class="btn">Read More</div>
  </article>
</main>

<footer>
  <div class="abs footer"></div>
  <h2 class="abs section-title" style="left:80px;top:999px">IT Support and Assistance Services</h2>
  <ul class="abs service-list" style="left:80px;top:1040px"><li>Proactive IT Support</li><li>Business Continuity</li><li>Disaster Recover</li></ul>
  <ul class="abs service-list" style="left:228px;top:1040px"><li>IT Network Support</li><li>Managed IT Services</li><li>ICT Support</li></ul>
  <ul class="abs service-list" style="left:375px;top:1040px"><li>IT Audit</li><li>Office Relocation</li><li>IT General Support</li></ul>

  <h2 class="abs section-title" style="left:542px;top:999px">Newsletter Sign Up</h2>
  <p class="abs newsletter-text" style="left:542px;top:1029px;width:220px">Aliquam congue fermentum nisl. Mauris accumsan nulla vel diam. Sed in lacus ut enim.</p>
  <div class="abs email">Email Address:</div>
  <div class="abs subscribe">Subscribe</div>

  <div class="abs base"></div>
  <p class="abs legal">Quill Harbor © Copyright 2012 | Privacy Policy<br>Home &nbsp;|&nbsp; About Us &nbsp;|&nbsp; Services &nbsp;|&nbsp; Testimonial &nbsp;|&nbsp; News &nbsp;|&nbsp; Contact Us</p>
  <span class="abs social" style="left:643px" aria-label="Social link"></span>
  <span class="abs social" style="left:672px" aria-label="Social link"></span>
  <span class="abs social" style="left:702px" aria-label="Social link"></span>
  <span class="abs social" style="left:732px" aria-label="Social link"></span>
</footer>

</body>
</html>
```